Yacht, Boats, Watersports company needs a redesign of business card

Hello Designers!
We are a Boat dealership company that sells fun in the water, we sell boats, Yachts, Kayaks and also yacht WaterSport toys. We are looking to redesign our business cards in to something a little bit more sophisticated. in a way that we can make better use of our company colors. I'm attaching a zipped file containing the company 3 sets of company logo which one is an horizontal another one is a vertical and also a chromed 3d logo. Also is included two set of business cards that we use and also some designs that i think it's interesting. We use PMS 2026c Orange and PMS 7687C Blue. I would like to see at least two different options with the orange as accent and also using blue as an accent color. It's really important for the business cards to have a font option and size that is legible to most people. Our current website is wwww.coralpennant.com. Please visit if you want to have a better feeling of the Boat dealership
You can send Single sided or double side options. We are now using single sided but we may be open for a double side option if we really like the design.
Target Market(s)
Marine, boat sales, yacht sales, water toys sales/
Contact Information for Business Card
Name: Dale Whitcombe
Address: 212 North Fenwick Lane,
Seabright Cove, FL 33090
Phone: 954-731-8842
Fax: 954:731-8843
Cell: 954-382-1490
Email: dw@coralpennant.com
Website: coralpennant.com
Requirements
Must have
- the current information of the business card provided.
logo
use the PMS Colors
Nice to have
- a touch of elegance and sophistication but simple
Should not have
- should not have any typography that is hard to read, the card should be simple but yet sophisticated.

```html
<!DOCTYPE html>
<html lang="en">
<head>
<meta charset="utf-8">
<title>Coral Pennant – Business Card</title>
<link href="https://fonts.googleapis.com/css2?family=Roboto+Condensed:wght@400;700&display=swap" rel="stylesheet">
<style>
  :root {
    --brand-blue: #1155a4;
    --brand-orange: #ee7127;
    --bleed-grey: #a7a7a7;
    --paper: #ffffff;
    --ink: #222222;
    --text-font: "Roboto Condensed", Arial, sans-serif;
  }
  html, body {
    margin: 0;
    width: 1200px;
    height: 1200px;
    overflow: hidden;
    background: var(--paper);
    font-family: var(--text-font);
  }
  .canvas { position: relative; width: 1200px; height: 1200px; }

  .bleed-area { position: absolute; background: var(--bleed-grey); }
  .bleed-label {
    position: absolute;
    font-size: 11px;
    color: var(--ink);
    line-height: 1;
  }
  .bleed-label--side { transform: rotate(90deg); transform-origin: left top; }

  /* Front */
  .card-front { left: 150px; top: 156px; width: 562px; height: 338px; }
  .front-face {
    position: absolute;
    left: 19px; top: 19px;
    width: 525px; height: 300px;
    background: var(--paper);
    border-radius: 33px;
  }
  .brand-mark {
    position: absolute;
    left: 50%; top: 62px;
    width: 70px; height: 70px;
    margin-left: -35px;
    box-sizing: border-box;
    border: 7px solid var(--brand-orange);
    border-radius: 50%;
  }
  .brand-name {
    position: absolute;
    left: 0; right: 0; top: 166px;
    text-align: center;
    font-weight: 700;
    font-size: 42px;
    letter-spacing: 6px;
    color: var(--brand-blue);
    text-transform: uppercase;
    line-height: 1;
  }
  .front-web {
    position: absolute;
    left: 0; right: 0; top: 270px;
    text-align: center;
    font-size: 14px;
    letter-spacing: 2.5px;
    color: var(--brand-blue);
  }

  /* Back */
  .card-back { left: 552px; top: 767px; width: 563px; height: 337px; }
  .name-band {
    position: absolute;
    left: 19px; top: 18px;
    width: 525px; height: 85px;
    background: var(--brand-blue);
    border-radius: 33px 33px 0 0;
    text-align: center;
  }
  .person-name {
    margin-top: 27px;
    font-weight: 700;
    font-size: 21px;
    color: var(--paper);
    letter-spacing: 0.5px;
    line-height: 1;
  }
  .person-title {
    margin-top: 6px;
    font-size: 12px;
    letter-spacing: 3.5px;
    color: var(--brand-orange);
    line-height: 1;
  }
  .contact-panel {
    position: absolute;
    left: 19px; top: 122px;
    width: 525px; height: 192px;
    background: var(--brand-orange);
    border-radius: 0 0 33px 33px;
  }
  .contact-list { position: absolute; left: 37px; top: 0; margin: 0; padding: 0; list-style: none; }
  .contact-item {
    position: absolute;
    left: 0;
    display: flex;
    align-items: center;
    gap: 10px;
    color: var(--paper);
    font-size: 14px;
    line-height: 16px;
    white-space: nowrap;
  }
  .contact-icon {
    width: 26px; height: 26px;
    border-radius: 50%;
    background: var(--brand-blue);
    flex: none;
    display: flex; align-items: center; justify-content: center;
  }
  .contact-divider {
    position: absolute;
    left: 352px; top: 27px;
    width: 1px; height: 140px;
    background: var(--paper);
  }
  .social-row {
    position: absolute;
    left: 390px; top: 84px;
    display: flex; gap: 8px;
  }
  .social-slot { width: 24px; height: 24px; background: var(--brand-blue); }
</style>
</head>
<body>
<div class="canvas">

  <section class="bleed-area card-front" aria-label="Card front">
    <div class="front-face">
      <div class="brand-mark"></div>
      <div class="brand-name">Coral Pennant</div>
      <div class="front-web">www.coralpennant.com</div>
    </div>
    <span class="bleed-label bleed-label--side" style="left:11px; top:146px;">bleed</span>
    <span class="bleed-label" style="left:208px; top:325px;">bleed</span>
  </section>

  <section class="bleed-area card-back" aria-label="Card back">
    <div class="name-band">
      <div class="person-name">DALE WHITCOMBE</div>
      <div class="person-title">CORPORATE MANAGER</div>
    </div>

    <div class="contact-panel">
      <ul class="contact-list">
        <li class="contact-item" style="top:10px;">
          <span class="contact-icon">
            <svg width="14" height="14" viewBox="0 0 14 14" aria-hidden="true"><path d="M3 1.5l2 2.5-1.2 1.3c.8 1.7 2.1 3 3.9 3.9L9 8l2.5 2-1 2c-4.5-.4-8.1-4-8.5-8.5z" fill="#fff"/></svg>
          </span>
          <span>1.555.731.8842<br>1.555.382.1490</span>
        </li>
        <li class="contact-item" style="top:57px;">
          <span class="contact-icon">
            <svg width="14" height="14" viewBox="0 0 14 14" aria-hidden="true"><rect x="4" y="1.5" width="6" height="3.5" fill="#fff"/><rect x="1.5" y="5.5" width="11" height="5" rx="1" fill="#fff"/><rect x="4" y="9" width="6" height="3.5" fill="#fff" stroke="#1155a4" stroke-width=".8"/></svg>
          </span>
          <span>1.555.731.8843</span>
        </li>
        <li class="contact-item" style="top:97px;">
          <span class="contact-icon">
            <svg width="14" height="14" viewBox="0 0 14 14" aria-hidden="true"><path d="M7 1.5l6 5.2h-2v5.8H8.3V9H5.7v3.5H3V6.7H1z" fill="#fff"/></svg>
          </span>
          <span>212 North Fenwick Lane<br>Seabright Cove, FL 33090</span>
        </li>
        <li class="contact-item" style="top:144px;">
          <span class="contact-icon">
            <svg width="14" height="14" viewBox="0 0 14 14" aria-hidden="true" fill="none" stroke="#fff" stroke-width="1.1"><circle cx="7" cy="7" r="5.5"/><ellipse cx="7" cy="7" rx="2.4" ry="5.5"/><path d="M1.5 7h11M2.5 4h9M2.5 10h9"/></svg>
          </span>
          <span>dw@coralpennant.com</span>
        </li>
      </ul>
      <div class="contact-divider"></div>
      <div class="social-row" aria-label="Social profiles">
        <span class="social-slot"></span>
        <span class="social-slot"></span>
        <span class="social-slot"></span>
      </div>
    </div>

    <span class="bleed-label bleed-label--side" style="left:12px; top:190px;">bleed</span>
    <span class="bleed-label" style="left:214px; top:322px;">bleed</span>
  </section>

</div>
</body>
</html>
```